design a construction company business card

Design business card around our logo. Card must have all the typical info: name, title, address, phone, email, business name, etc. Somewhere on the card I would like to see our motto "Built on integrity... Inspired by commitment." Consider adding a splash of bright orange to the card to complement the blues and silvers/grays in the logo. We are open to metallic inks, textures, etc. We would like to see options on both light and dark backgrounds. The font in the logo is Euro Technic Extended Regular.

```html
<!DOCTYPE html>
<html lang="en">
<head>
<meta charset="utf-8">
<title>Hollis Builders – Business Card</title>
<link rel="stylesheet" href="https://fonts.googleapis.com/css2?family=Michroma&family=Arimo:wght@400;700&display=swap">
<style>
  :root {
    --stage: #1c1c1f;
    --blue-light: #1f6fbf;
    --blue-deep: #243f95;
    --blue-brand: #2a4fb0;
    --white: #ffffff;
    --ink-grey: #6f7378;
    --shadow: rgba(0,0,0,.55);
  }
  * { box-sizing: border-box; margin: 0; padding: 0; }
  html, body { width: 1200px; height: 800px; overflow: hidden; }
  body {
    background: var(--stage);
    position: relative;
    font-family: "Arimo", Arial, sans-serif;
  }
  .card {
    position: absolute;
    width: 560px;
    height: 320px;
    box-shadow: 0 18px 40px var(--shadow);
    overflow: hidden;
  }
  .card--front {
    left: 90px; top: 80px;
    background: linear-gradient(160deg, var(--blue-light) 0%, var(--blue-deep) 70%);
    display: flex; flex-direction: column; align-items: center; justify-content: center;
    color: var(--white);
  }
  .wordmark {
    display: flex; align-items: center; gap: 14px;
  }
  .wordmark__mark {
    width: 18px; height: 18px; background: currentColor;
  }
  .wordmark__name {
    font-family: "Michroma", sans-serif;
    font-size: 40px; letter-spacing: 2px; line-height: 1;
  }
  .wordmark__sub {
    font-family: "Michroma", sans-serif;
    font-size: 12px; letter-spacing: 3px; margin-top: 10px;
  }
  .front__web {
    margin-top: 22px; font-weight: 700; font-size: 15px; letter-spacing: 2px;
  }

  .card--back {
    left: 560px; top: 420px;
    display: flex;
    background: var(--white);
  }
  .back__brand {
    width: 44%;
    display: flex; flex-direction: column; align-items: center; justify-content: center;
    color: var(--blue-brand);
  }
  .back__brand .wordmark__name { font-size: 24px; letter-spacing: 1px; }
  .back__brand .wordmark { gap: 8px; }
  .back__brand .wordmark__mark { width: 12px; height: 12px; }
  .back__brand .wordmark__sub { font-size: 8px; letter-spacing: 2px; color: var(--blue-brand); }
  .back__details {
    width: 56%;
    background: linear-gradient(165deg, var(--blue-light) 0%, var(--blue-deep) 65%);
    border-left: 4px solid #9aa3ad;
    color: var(--white);
    padding: 56px 28px 0 34px;
  }
  .person__name {
    font-family: "Michroma", sans-serif; font-size: 19px; letter-spacing: 1px;
  }
  .person__title { font-size: 14px; margin-top: 2px; }
  .contact { list-style: none; margin-top: 18px; font-size: 13px; line-height: 1.45; }
  .contact__item { display: flex; align-items: center; gap: 7px; }
  .contact__icon { width: 15px; height: 15px; flex: none; }
  .motto { margin-top: 12px; font-weight: 700; font-size: 13.5px; line-height: 1.4; }
</style>
</head>
<body>
  <section class="card card--front" aria-label="Card front">
    <div class="wordmark">
      <span class="wordmark__mark"></span>
      <span class="wordmark__name">HOLLIS</span>
    </div>
    <div class="wordmark__sub">BUILDERS, INC.</div>
    <div class="front__web">www.hollisbuilders.com</div>
  </section>

  <section class="card card--back" aria-label="Card back">
    <div class="back__brand">
      <div class="wordmark">
        <span class="wordmark__mark"></span>
        <span class="wordmark__name">HOLLIS</span>
      </div>
      <div class="wordmark__sub">BUILDERS, INC.</div>
    </div>
    <div class="back__details">
      <h1 class="person__name">MARCUS DALE</h1>
      <p class="person__title">Founder</p>
      <ul class="contact">
        <li>PO Box 48</li>
        <li>Harbour Road, Geelong</li>
        <li class="contact__item">
          <svg class="contact__icon" viewBox="0 0 16 16" aria-hidden="true"><circle cx="8" cy="8" r="7.5" fill="#fff"/><rect x="5.5" y="3.5" width="5" height="9" rx="1" fill="none" stroke="#243f95" stroke-width="1.3"/></svg>
          555 210 4400
        </li>
        <li class="contact__item">
          <svg class="contact__icon" viewBox="0 0 16 16" aria-hidden="true"><circle cx="8" cy="8" r="7.5" fill="#fff"/><rect x="4" y="5" width="8" height="6" fill="none" stroke="#243f95" stroke-width="1.2"/><path d="M4 5l4 3.5L12 5" fill="none" stroke="#243f95" stroke-width="1.2"/></svg>
          hello@hollisbuilders.com
        </li>
      </ul>
      <p class="motto">Built on integrity...<br>Inspired by commitment.</p>
    </div>
  </section>
</body>
</html>
```